Redesign of business card for Cedar Ridge Mechanical

We are looking for a new design for our business cards for Cedar Ridge Mechanical. We are a plumbing & HVAC construction company, operating on the West Coast of Canada and USA. Logo attached.
Industry/Entity Type
Construction - Plumbing & HVAC
Contact Information for Business Card
Name, address, phone numbers, email, website address
Look and feel
Each slider illustrates characteristics of the customer's brand and the style your logo design should communicate.

```html
<!DOCTYPE html>
<html lang="en">
<head>
<meta charset="UTF-8">
<title>Cedar Ridge Mechanical – Business Card</title>
<link href="https://fonts.googleapis.com/css2?family=Montserrat:wght@400;700&family=Oswald:wght@500&display=swap" rel="stylesheet">
<style>
  :root {
    --stage: #2b2b2b;
    --ink: #0a0a0a;
    --paper: #ffffff;
    --grey: #8e9091;
    --text: #1a1a1a;
    --muted: #3a3a3a;
  }
  * { margin: 0; padding: 0; box-sizing: border-box; }
  html, body { width: 1200px; height: 880px; overflow: hidden; }
  body {
    background: var(--stage);
    position: relative;
    font-family: "Montserrat", sans-serif;
  }
  .card {
    position: absolute;
    left: 290px;
    width: 620px;
    height: 354px;
    border-radius: 26px;
    overflow: hidden;
  }
  .card--front { top: 60px; background: var(--ink); }
  .card--back { top: 466px; background: var(--paper); }

  .wordmark {
    position: absolute;
    display: flex;
    align-items: center;
    font-family: "Oswald", sans-serif;
    font-weight: 500;
    text-transform: uppercase;
    letter-spacing: 1px;
    white-space: nowrap;
  }
  .wordmark__square { display: block; flex: none; }
  .card--front .wordmark {
    left: 0; right: 0; top: 0; bottom: 0;
    justify-content: center;
    gap: 16px;
    color: var(--paper);
    font-size: 38px;
  }
  .card--front .wordmark__square { width: 34px; height: 34px; background: var(--paper); }
  .card--back .wordmark {
    left: 30px; top: 134px;
    width: 290px;
    gap: 10px;
    color: var(--ink);
    font-size: 21px;
    letter-spacing: 0.5px;
  }
  .card--back .wordmark__square { width: 18px; height: 18px; background: var(--ink); }

  .divider {
    position: absolute;
    left: 342px; top: 52px;
    width: 1px; height: 200px;
    background: var(--ink);
  }
  .contact {
    position: absolute;
    left: 362px; top: 44px;
    color: var(--text);
  }
  .contact__name {
    font-weight: 700;
    font-size: 24px;
    letter-spacing: 1px;
    color: var(--ink);
  }
  .contact__role { font-size: 15px; color: var(--muted); margin-top: 2px; }
  .contact__address { font-size: 15px; color: var(--muted); margin-top: 14px; line-height: 1.35; }
  .contact__list { list-style: none; margin-top: 10px; }
  .contact__item {
    display: flex; align-items: center; gap: 8px;
    font-size: 15px; color: var(--muted); line-height: 1.55;
  }
  .contact__icon { width: 13px; height: 13px; flex: none; fill: var(--ink); }

  .bands { position: absolute; left: 0; bottom: 0; width: 620px; height: 120px; }
</style>
</head>
<body>
  <section class="card card--front" aria-label="Card front">
    <div class="wordmark"><span class="wordmark__square"></span>Cedar Ridge Mechanical</div>
  </section>

  <section class="card card--back" aria-label="Card back">
    <div class="wordmark"><span class="wordmark__square"></span>Cedar Ridge Mechanical</div>
    <div class="divider"></div>
    <div class="contact">
      <h1 class="contact__name">MARCUS HALE</h1>
      <p class="contact__role">Managing Director</p>
      <p class="contact__address">Your address, City<br>State, Zip 1234</p>
      <ul class="contact__list">
        <li class="contact__item">
          <svg class="contact__icon" viewBox="0 0 16 16"><path d="M3 2h3l1 4-2 1a9 9 0 0 0 4 4l1-2 4 1v3a1 1 0 0 1-1 1A13 13 0 0 1 2 3a1 1 0 0 1 1-1z"/></svg>
          123 456 789
        </li>
        <li class="contact__item">
          <svg class="contact__icon" viewBox="0 0 16 16"><path d="M1 3h14v10H1z M2 4l6 5 6-5" fill="none" stroke="#0a0a0a" stroke-width="1.6"/></svg>
          info@yourgmail.com
        </li>
        <li class="contact__item">
          <svg class="contact__icon" viewBox="0 0 16 16"><circle cx="8" cy="8" r="7"/></svg>
          www.yourwebsite.com
        </li>
      </ul>
    </div>
    <svg class="bands" viewBox="0 0 620 120" aria-hidden="true">
      <path d="M0 62 H400 Q416 62 412 76 L400 112 H0 Z" fill="#0a0a0a"/>
      <path d="M430 56 Q436 36 456 36 H620 V80 H418 Z" fill="#8e9091"/>
    </svg>
  </section>
</body>
</html>
```